Business Card Design Project

We are not a new company, but renamed to "Vantorin Kitchens" last year. We specialize in modern high-end cabinetry imports. We would like to communicate a sense of quality and cutting edge technology. Ideally the design would incorporate our logo colors, silver, red and preferably a black, matte background. Though we are open to suggestions.
Logo is attached.
Edit: I have attached rough drafts of the previous cards, this way you will have all necessary content that needs to go on the cards.
Updates
Project Deadline Extended
Reason: We have received a lot of great designs, but due to the sheer number we couldn't respond to all. We will extend the deadline for another 7 days to finalize and provide feedback to designers.
Thank you for your hard work!
Industry/Entity Type
Business
Look and feel
Each slider illustrates characteristics of the customer's brand and the style your logo design should communicate.

```html
<!DOCTYPE html>
<html lang="en">
<head>
<meta charset="utf-8">
<title>Vantorin Kitchens — Business Card</title>
<link rel="stylesheet" href="https://fonts.googleapis.com/css2?family=Noto+Serif:wght@700&family=Open+Sans:wght@400&display=swap">
<style>
  :root {
    --stage: #ece9e6;
    --red-deep: #7a0a14;
    --red: #c8102e;
    --red-bright: #e0203a;
    --shadow-edge: #3a0408;
    --paper: #ffffff;
    --paper-shade: #e6e6e6;
    --ink: #5e5e5e;
    --ink-soft: #777777;
    --frame: #c4203a;
  }
  * { box-sizing: border-box; margin: 0; padding: 0; }
  html, body { width: 1200px; height: 750px; overflow: hidden; }
  body {
    background: var(--stage);
    position: relative;
    font-family: "Open Sans", sans-serif;
  }
  .card {
    position: absolute;
    left: 295px;
    width: 611px;
    height: 330px;
    border-radius: 20px;
    overflow: hidden;
    box-shadow: 0 4px 12px rgba(0,0,0,0.25);
    background: var(--paper);
  }
  .card--front { top: 19px; }
  .card--back { top: 390px; }
  .card__art { position: absolute; inset: 0; width: 100%; height: 100%; }

  .holder-name {
    position: absolute;
    left: 348px;
    top: 168px;
    transform: translateX(-50%);
    font-family: "Noto Serif", serif;
    font-weight: 700;
    font-size: 38px;
    color: var(--ink);
    white-space: nowrap;
    line-height: 1;
  }
  .holder-role {
    position: absolute;
    left: 348px;
    top: 216px;
    transform: translateX(-50%);
    font-family: "Noto Serif", serif;
    font-weight: 700;
    font-size: 11px;
    letter-spacing: 2.5px;
    color: var(--ink);
  }
  .contact-box {
    position: absolute;
    left: 109px;
    top: 238px;
    width: 482px;
    height: 83px;
    border: 2px solid var(--frame);
    border-radius: 9px;
    background: var(--paper);
    padding: 5px 10px;
    list-style: none;
  }
  .contact-box li {
    font-size: 12.5px;
    line-height: 13.6px;
    color: var(--ink-soft);
  }
  .brand-name {
    position: absolute;
    left: 36px;
    top: 86px;
    font-family: "Noto Serif", serif;
    font-weight: 700;
    font-size: 40px;
    color: var(--ink);
    white-space: nowrap;
    line-height: 1;
  }
</style>
</head>
<body>

<section class="card card--front">
  <svg class="card__art" viewBox="0 0 611 330" preserveAspectRatio="none" aria-hidden="true">
    <defs>
      <linearGradient id="frontRed" x1="0" y1="0" x2="0" y2="1">
        <stop offset="0" stop-color="var(--red-deep)"/>
        <stop offset="0.5" stop-color="var(--red)"/>
        <stop offset="1" stop-color="var(--red-deep)"/>
      </linearGradient>
      <radialGradient id="frontPaper" cx="0.55" cy="0.55" r="0.7">
        <stop offset="0.5" stop-color="var(--paper)"/>
        <stop offset="1" stop-color="var(--paper-shade)"/>
      </radialGradient>
    </defs>
    <rect width="611" height="330" fill="url(#frontRed)"/>
    <path d="M0,122 Q300,20 611,150 L611,330 L0,330 Z" fill="var(--shadow-edge)" opacity="0.8"/>
    <path d="M0,129 Q300,31 611,157 L611,330 L0,330 Z" fill="url(#frontPaper)"/>
  </svg>
  <h1 class="holder-name">Marek Dolan</h1>
  <p class="holder-role">DIRECTOR</p>
  <ul class="contact-box">
    <li>Adress:</li>
    <li>Phone:</li>
    <li>Cell:</li>
    <li>Fax:</li>
    <li>Email:</li>
  </ul>
</section>

<section class="card card--back">
  <svg class="card__art" viewBox="0 0 611 330" preserveAspectRatio="none" aria-hidden="true">
    <defs>
      <linearGradient id="backRed" x1="0" y1="0" x2="0" y2="1">
        <stop offset="0" stop-color="var(--red-deep)"/>
        <stop offset="0.45" stop-color="var(--red-bright)"/>
        <stop offset="1" stop-color="var(--red-deep)"/>
      </linearGradient>
      <radialGradient id="backPaper" cx="0.45" cy="0.35" r="0.75">
        <stop offset="0.5" stop-color="var(--paper)"/>
        <stop offset="1" stop-color="var(--paper-shade)"/>
      </radialGradient>
    </defs>
    <rect width="611" height="330" fill="url(#backPaper)"/>
    <path d="M0,150 Q300,306 611,172 L611,330 L0,330 Z" fill="var(--shadow-edge)" opacity="0.85"/>
    <path d="M0,158 Q300,316 611,182 L611,330 L0,330 Z" fill="url(#backRed)"/>
  </svg>
  <p class="brand-name">Vantorin Kitchens</p>
</section>

</body>
</html>
```